Business card for medical clinic

I need an upmarket, modern medical/health business card for my clinic

Contact Information for Business Card

name, address, email, qr code

```html
<!DOCTYPE html>
<html lang="en">
<head>
<meta charset="utf-8">
<title>Corvale Health Partners – Business Card</title>
<link href="https://fonts.googleapis.com/css2?family=Montserrat:wght@400;500;800&display=swap" rel="stylesheet">
<style>
  :root {
    --stage: #2b2b2d;
    --ink: #0c0c0d;
    --paper: #ffffff;
    --brand: #1c74ad;
    --brand-deep: #1a5585;
    --brand-light: #2ba6e0;
    --muted: #2e2e2e;
  }
  * { box-sizing: border-box; margin: 0; padding: 0; }
  html, body {
    width: 1200px; height: 880px; overflow: hidden;
    background: var(--stage);
    font-family: "Montserrat", sans-serif;
  }
  .stage { position: relative; width: 1200px; height: 880px; }

  .card {
    position: absolute;
    width: 560px; height: 320px;
    border-radius: 22px;
    overflow: hidden;
    background: var(--paper);
    box-shadow: 0 18px 40px rgba(0,0,0,.45);
  }

  /* Front */
  .card--front { left: 80px; top: 70px; }
  .front__panel { position: absolute; inset: 0; }
  .front__brand {
    position: absolute; left: 150px; top: 160px;
    font-weight: 500; font-size: 27px; letter-spacing: 3px;
    color: var(--brand); line-height: 1.15; text-transform: uppercase;
  }

  /* Back */
  .card--back { left: 560px; top: 490px; }
  .back__panel { position: absolute; inset: 0; }
  .back__person { position: absolute; right: 34px; top: 30px; text-align: right; }
  .back__name {
    font-weight: 800; font-size: 22px; letter-spacing: 1px;
    color: var(--brand); text-transform: uppercase;
  }
  .back__role { font-size: 13px; color: var(--muted); margin-top: 2px; }
  .back__accent {
    position: absolute; right: 0; top: 26px;
    width: 18px; height: 44px;
    background: linear-gradient(180deg, var(--brand-light), var(--brand-deep));
  }
  .back__brand {
    position: absolute; left: 40px; top: 112px;
    font-weight: 500; font-size: 21px; letter-spacing: 2px;
    color: var(--brand); text-transform: uppercase; line-height: 1.2;
  }
  .back__address {
    position: absolute; left: 40px; top: 182px;
    font-size: 14px; line-height: 1.4; color: var(--muted);
  }
  .back__contacts {
    position: absolute; left: 40px; top: 242px;
    list-style: none;
  }
  .back__contacts li {
    display: flex; align-items: center; gap: 9px;
    font-size: 13.5px; color: var(--paper); height: 22px;
  }
  .back__contacts svg { width: 14px; height: 14px; flex: none; }
</style>
</head>
<body>
<main class="stage">

  <section class="card card--front" aria-label="Card front">
    <svg class="front__panel" viewBox="0 0 560 320" aria-hidden="true">
      <path d="M0 0 H150 V0 L175 128 H0 Z" fill="none"/>
      <path d="M0 110 L160 110 L160 240 L300 240 L330 320 L0 320 Z" fill="var(--ink)"/>
      <circle cx="150" cy="205" r="118" fill="var(--paper)"/>
    </svg>
    <p class="front__brand">Corvale Health<br>Partners</p>
  </section>

  <section class="card card--back" aria-label="Card back">
    <svg class="back__panel" viewBox="0 0 560 320" aria-hidden="true">
      <path d="M0 232 H220 L240 170 H560 V320 H0 Z" fill="var(--ink)"/>
      <circle cx="530" cy="170" r="52" fill="var(--paper)"/>
    </svg>
    <div class="back__accent"></div>
    <div class="back__person">
      <p class="back__name">Daniel Hart</p>
      <p class="back__role">Managing Director</p>
    </div>
    <p class="back__brand">Corvale Health<br>Partners</p>
    <p class="back__address">Your address, City<br>State, Zip 1234</p>
    <ul class="back__contacts">
      <li>
        <svg viewBox="0 0 16 16" aria-hidden="true"><path d="M3 1.5h3l1.2 3.3-1.8 1.2a8 8 0 0 0 4.6 4.6l1.2-1.8 3.3 1.2v3c0 .6-.5 1.1-1.1 1.1A12.5 12.5 0 0 1 1.9 2.6c0-.6.5-1.1 1.1-1.1Z" fill="var(--brand-light)"/></svg>
        123 456 789
      </li>
      <li>
        <svg viewBox="0 0 16 16" aria-hidden="true"><rect x="1" y="3" width="14" height="10" rx="1.5" fill="var(--brand-light)"/><path d="M1.5 4 8 9l6.5-5" stroke="var(--ink)" stroke-width="1.3" fill="none"/></svg>
        info@youremail.com
      </li>
      <li>
        <svg viewBox="0 0 16 16" aria-hidden="true"><circle cx="8" cy="8" r="6.5" fill="var(--brand-light)"/><path d="M1.5 8h13M8 1.5c-2.5 3-2.5 10 0 13M8 1.5c2.5 3 2.5 10 0 13" stroke="var(--ink)" stroke-width="1" fill="none"/></svg>
        www.yourwebsite.com
      </li>
    </ul>
  </section>

</main>
</body>
</html>
```